Website for steady harbor detailing.

Need a homepage, pages for: car and truck detailing, boat detailing, airplane detailing, about us, contact us. I have the domain name through nimbushelm so I will need the design uploaded on my domain. Also hoping to link other domains to this page.I would like to see the logo more pronounced. I would like to see a large phone number link to call my business. The layout looks nice but the pics need to depict car washing and waxing not car mechanics. i would like the colors of the webpage to incorporate the colors found in the logo in some way. I would like links to social media pages
Updates

Target Market(s)

Local customers in pelican cove Beach, Florida.

Number of Pages Required

5+ page

Colors

Requirements
Must have
• Easy to navigate, attractive pages with pictures and logo, professional looking. must have my phone number and logo very prevalent and links to call or go to home page. I would like links to my social media accounts on the home page.
Nice to have
• Easy to navigate, attractive pages with pictures and logo, professional looking.

```html
<!DOCTYPE html>
<html lang="en">
<head>
<meta charset="utf-8">
<title>Steady Harbor Detailing</title>
<link rel="stylesheet" href="https://fonts.googleapis.com/css2?family=Montserrat:wght@400;500;600;700&family=Open+Sans:wght@400;600&display=swap">
<style>
:root{
  --red:#e3151f;
  --red-dark:#c9101a;
  --blue:#1b8fe0;
  --blue-bright:#1a9bf0;
  --navy:#1f2470;
  --navy-deep:#262a7c;
  --ink:#333333;
  --muted:#777777;
  --white:#ffffff;
  --line:#e6e6e6;
}
*{box-sizing:border-box;margin:0;padding:0}
html,body{width:1200px;height:2236px;overflow:hidden;background:var(--white)}
body{font-family:"Open Sans",Arial,sans-serif;color:var(--ink);position:relative}
.canvas{position:relative;width:1200px;height:2236px;overflow:hidden}
.abs{position:absolute}
a{color:inherit;text-decoration:none}

/* header */
.site-header{left:0;top:0;width:1200px;height:113px;background:var(--white)}
.brand{left:119px;top:24px;display:flex;align-items:center;gap:12px}
.brand-mark{width:40px;height:40px;border-radius:50%;background:var(--red);flex:none}
.brand-name{font-family:"Montserrat",Arial,sans-serif;font-weight:700;font-size:25px;line-height:1.05;color:var(--navy)}
.header-phone{left:858px;top:0;width:208px;height:40px;background:var(--red);color:var(--white);
  font-family:"Montserrat",Arial,sans-serif;font-size:21px;font-weight:500;display:flex;align-items:center;justify-content:center;gap:6px}
.main-nav{right:133px;top:61px;display:flex;gap:33px;font-family:"Montserrat",Arial,sans-serif;font-size:17px;color:#222}

/* hero */
.hero{left:0;top:113px;width:1200px;height:500px;
  background:linear-gradient(100deg,#4b4f55 0%,#8a9096 45%,#5b6066 75%,#3e4247 100%)}
.hero-title{left:121px;top:226px;font-family:"Montserrat",Arial,sans-serif;font-weight:700;font-size:40px;line-height:46px;color:var(--white);text-transform:uppercase}
.hero-sub{left:123px;top:338px;width:440px;font-family:"Montserrat",Arial,sans-serif;font-size:18px;line-height:25px;color:var(--white)}
.hero-call{left:109px;top:404px;width:423px;height:63px;border-radius:32px;background:rgba(40,40,44,.72);display:flex;align-items:center;padding-left:36px}
.hero-call .num{font-family:"Montserrat",Arial,sans-serif;font-weight:600;font-size:28px;color:var(--white);display:flex;align-items:center;gap:10px}
.btn-call{position:absolute;left:276px;top:9px;width:131px;height:42px;border-radius:21px;background:linear-gradient(var(--blue-bright),#0f78cc);
  color:var(--white);font-family:"Montserrat",Arial,sans-serif;font-size:17px;display:flex;align-items:center;justify-content:center}
.slider-dots{left:561px;top:567px;display:flex;gap:9px}
.slider-dots span{width:14px;height:14px;border-radius:50%;background:var(--white)}
.slider-dots span.active{background:transparent;border:2px solid var(--white)}

/* intro */
.section-title{font-family:"Montserrat",Arial,sans-serif;font-weight:500;text-align:center;width:1200px;left:0}
.intro-title{top:659px;font-size:35px;color:var(--blue)}
.intro-title .u{position:relative}
.intro-title .u::after{content:"";position:absolute;left:0;right:0;bottom:-6px;height:3px;background:var(--blue)}
.intro-text{left:175px;top:719px;width:888px;text-align:center;font-size:15.5px;line-height:23px;color:#555}
.category{width:244px;height:244px;border-radius:50%;background:var(--white);box-shadow:0 4px 18px rgba(0,0,0,.16);
  display:flex;flex-direction:column;align-items:center;justify-content:center;top:833px}
.category svg{width:110px;height:90px}
.category .label{font-family:"Montserrat",Arial,sans-serif;font-weight:500;font-size:20px;margin-top:14px}
.cat-car{left:196px}.cat-car .label{color:var(--red)}
.cat-boat{left:486px}.cat-boat .label{color:var(--navy)}
.cat-plane{left:775px}.cat-plane .label{color:var(--blue)}

/* services */
.services{left:0;top:1125px;width:1200px;height:495px;background:linear-gradient(115deg,#1791e8 0%,#1a6fcf 40%,var(--navy-deep) 100%)}
.services-title{top:1169px;font-size:32px;color:var(--white)}
.title-rule{height:3px;background:var(--white);width:70px;left:565px}
.service-card{top:1245px;width:303px;height:313px;background:var(--white);box-shadow:0 3px 10px rgba(0,0,0,.2)}
.service-card .photo{width:100%;height:176px}
.service-card h3{font-family:"Montserrat",Arial,sans-serif;font-weight:600;font-size:21px;color:var(--blue);text-align:center;margin-top:13px}
.service-card p{font-size:13.5px;line-height:20px;color:var(--muted);text-align:center;padding:6px 36px 0}
.btn-more{position:absolute;left:80px;bottom:-18px;width:142px;height:36px;background:linear-gradient(#f0222c,var(--red-dark));color:var(--white);
  font-family:"Montserrat",Arial,sans-serif;font-size:15px;display:flex;align-items:center;justify-content:center;box-shadow:0 2px 5px rgba(0,0,0,.25)}
.card-wash{left:118px}.card-wax{left:443px}.card-degrease{left:775px}
.photo-wash{background:linear-gradient(135deg,#9cc3e6,#c9ccd1 50%,#7d8084)}
.photo-wax{background:linear-gradient(135deg,#b8121a,#e0262d 55%,#7a0c10)}
.photo-degrease{background:linear-gradient(135deg,#2f3237,#6b6f75 55%,#3a3d42)}

/* call band */
.call-band{left:0;top:1620px;width:1200px;height:90px;background:var(--white)}
.call-band .lead{left:240px;top:1650px;font-family:"Montserrat",Arial,sans-serif;font-size:25px;color:#555}
.call-pill{left:583px;top:1641px;width:358px;height:49px;border:2px solid var(--red);border-radius:25px;display:flex;align-items:center;padding-left:20px}
.call-pill .num{font-family:"Montserrat",Arial,sans-serif;font-weight:700;font-size:24px;color:var(--navy);display:flex;align-items:center;gap:8px}
.btn-call-navy{position:absolute;right:6px;top:6px;width:112px;height:33px;border-radius:17px;background:linear-gradient(#2a2f8a,#15185a);
  color:var(--white);font-family:"Montserrat",Arial,sans-serif;font-size:14px;display:flex;align-items:center;justify-content:center}

/* testimonials */
.testimonials{left:0;top:1710px;width:1200px;height:401px;background:linear-gradient(90deg,#ef4a4f 0%,#e52a31 50%,#d9101a 100%)}
.testimonials-title{top:1750px;font-size:32px;color:var(--white)}
.testimonials .rule{left:565px;top:88px;width:70px;height:3px;background:rgba(255,255,255,.6)}
.quote-card{top:1835px;width:422px;height:206px;border:1px solid rgba(255,255,255,.55);text-align:center;color:var(--white)}
.quote-card .mark{font-family:"Montserrat",Arial,sans-serif;font-weight:700;font-size:46px;line-height:40px;margin-top:50px}
.quote-card p{font-family:"Montserrat",Arial,sans-serif;font-size:14.5px;line-height:19px;padding:6px 44px 0}
.quote-card .author{font-family:"Montserrat",Arial,sans-serif;font-weight:600;font-size:14.5px;margin-top:12px}
.quote-a{left:176px}.quote-b{left:614px}
.avatar{width:88px;height:88px;border-radius:50%;border:4px solid var(--white);background:linear-gradient(#d8c4b4,#a88f7e);top:1790px}
.avatar-a{left:344px}.avatar-b{left:780px}
.arrow{top:1916px}

/* footer */
.footer-nav{left:122px;top:2146px;display:flex;gap:19px;font-family:"Montserrat",Arial,sans-serif;font-size:15.5px;color:#333}
.copyright{left:122px;top:2182px;font-family:"Montserrat",Arial,sans-serif;font-size:13.5px;color:#444}
.footer-phone{left:678px;top:2143px;font-family:"Montserrat",Arial,sans-serif;font-weight:700;font-size:21px;color:var(--navy);display:flex;align-items:center;gap:6px}
.social{left:866px;top:2144px;display:flex;gap:6px}
.social a{width:36px;height:36px;border-radius:50%;display:block}
.s1{background:#3b5998}.s2{background:#55acee}.s3{background:#3f5d82}.s4{background:#0e76a8}.s5{background:var(--red)}
</style>
</head>
<body>
<div class="canvas">

  <header class="site-header abs">
    <a class="brand abs" href="#home">
      <span class="brand-mark"></span>
      <span class="brand-name">Steady Harbor<br>Detailing</span>
    </a>
    <a class="header-phone abs" href="tel:5550104827">
      <svg width="18" height="18" viewBox="0 0 24 24"><path fill="#fff" d="M6.6 10.8a15.1 15.1 0 0 0 6.6 6.6l2.2-2.2c.3-.3.7-.4 1-.2 1.1.4 2.3.6 3.6.6.6 0 1 .4 1 1V20c0 .6-.4 1-1 1C10.6 21 3 13.4 3 4c0-.6.4-1 1-1h3.5c.6 0 1 .4 1 1 0 1.3.2 2.5.6 3.6.1.3 0 .7-.2 1z"/></svg>
      555-010-4827
    </a>
    <nav class="main-nav abs">
      <a href="#about">About</a><a href="#services">Services</a><a href="#car">Car</a><a href="#boat">Boat</a><a href="#airplanes">Airplanes</a><a href="#testimonials">Testimonials</a><a href="#contact">Contact</a>
    </nav>
  </header>

  <section class="hero abs" role="img" aria-label="Photo of a silver car being rinsed with a pressure washer"></section>
  <h1 class="hero-title abs">Car Washing and<br>Waxing Services</h1>
  <p class="hero-sub abs">Class aptent taciti sociosqu ad litora torquent per conubia nostra per inceptos</p>
  <div class="hero-call abs">
    <span class="num">
      <svg width="24" height="24" viewBox="0 0 24 24"><path fill="#fff" d="M6.6 10.8a15.1 15.1 0 0 0 6.6 6.6l2.2-2.2c.3-.3.7-.4 1-.2 1.1.4 2.3.6 3.6.6.6 0 1 .4 1 1V20c0 .6-.4 1-1 1C10.6 21 3 13.4 3 4c0-.6.4-1 1-1h3.5c.6 0 1 .4 1 1 0 1.3.2 2.5.6 3.6.1.3 0 .7-.2 1z"/></svg>
      555-010-4827
    </span>
    <a class="btn-call" href="tel:5550104827">Call Us</a>
  </div>
  <div class="slider-dots abs"><span class="active"></span><span></span><span></span><span></span></div>

  <h2 class="section-title intro-title abs">Steady Harbor <span class="u">Detailing</span></h2>
  <p class="intro-text abs">Our main business is detailing cars, boats, and airplanes. Wash, wax, degrease, we do it all. Iwould like a separate page for cars, boats, and airplanes. My business is located in Pelican Cove Florida in Palm Shore County.I would like to emphasize that I have been in pelican cove for over 30 years and that this business is locally owned and operated.</p>

  <a class="category cat-car abs" href="#car">
    <svg viewBox="0 0 110 90" aria-hidden="true">
      <path fill="#e3151f" d="M22 40 L30 22 Q32 18 37 18 H73 Q78 18 80 22 L88 40 Q98 42 98 52 V70 H88 V78 H76 V70 H34 V78 H22 V70 H12 V52 Q12 42 22 40 Z"/>
      <path fill="#fff" d="M30 40 L36 25 H74 L80 40 Z"/>
      <circle cx="25" cy="54" r="5" fill="#fff"/><circle cx="85" cy="54" r="5" fill="#fff"/>
      <rect x="40" y="52" width="30" height="10" fill="#fff"/>
    </svg>
    <span class="label">CAR</span>
  </a>
  <a class="category cat-boat abs" href="#boat">
    <svg viewBox="0 0 110 90" aria-hidden="true" fill="none" stroke="#1f2470" stroke-width="3">
      <path d="M52 8 V60"/><path d="M52 10 L30 50 H52"/><path d="M56 16 L74 50 H56"/>
      <path d="M14 60 H96 L86 76 H26 Z"/><path d="M20 84 Q30 80 40 84 T60 84 T80 84 T96 84"/>
    </svg>
    <span class="label">BOAT</span>
  </a>
  <a class="category cat-plane abs" href="#airplanes">
    <svg viewBox="0 0 110 90" aria-hidden="true" fill="none" stroke="#1b8fe0" stroke-width="3.5" stroke-linejoin="round">
      <path d="M8 38 H30 L20 24 H30 L44 38 H84 Q100 38 100 46 Q100 54 84 54 H56 L40 76 H28 L38 54 H20 L14 62 H6 L10 46 Z"/>
      <path d="M44 38 L32 14 H44 L62 38"/>
    </svg>
    <span class="label">AIRPLANE</span>
  </a>

  <section class="services abs" id="services"></section>
  <h2 class="section-title services-title abs">Our Services</h2>
  <div class="title-rule abs" style="top:1212px"></div>

  <article class="service-card card-wash abs">
    <div class="photo photo-wash" role="img" aria-label="Photo of a car being washed with a spray hose"></div>
    <h3>Washing</h3>
    <p>Aget tempor cursus neque mi consectetuer mi a ultricies massa est sed nisl Class aptent taciti</p>
    <a class="btn-more" href="#washing">Read More</a>
  </article>
  <article class="service-card card-wax abs">
    <div class="photo photo-wax" role="img" aria-label="Photo of wax being applied to a red car with a sponge"></div>
    <h3>Wax</h3>
    <p>Aget tempor cursus neque mi consectetuer mi a ultricies massa est sed nisl Class aptent taciti</p>
    <a class="btn-more" href="#wax">Read More</a>
  </article>
  <article class="service-card card-degrease abs">
    <div class="photo photo-degrease" role="img" aria-label="Photo of a polishing machine on a dark car panel"></div>
    <h3>Degrease</h3>
    <p>Aget tempor cursus neque mi consectetuer mi a ultricies massa est sed nisl Class aptent taciti</p>
    <a class="btn-more" href="#degrease">Read More</a>
  </article>

  <section class="call-band abs"></section>
  <p class="lead abs" style="left:240px;top:1650px;font-family:'Montserrat',Arial,sans-serif;font-size:25px;color:#555">Call Us Now for any Enquiry</p>
  <div class="call-pill abs">
    <span class="num">
      <svg width="22" height="22" viewBox="0 0 24 24"><path fill="#e3151f" d="M6.6 10.8a15.1 15.1 0 0 0 6.6 6.6l2.2-2.2c.3-.3.7-.4 1-.2 1.1.4 2.3.6 3.6.6.6 0 1 .4 1 1V20c0 .6-.4 1-1 1C10.6 21 3 13.4 3 4c0-.6.4-1 1-1h3.5c.6 0 1 .4 1 1 0 1.3.2 2.5.6 3.6.1.3 0 .7-.2 1z"/></svg>
      555-010-4827
    </span>
    <a class="btn-call-navy" href="tel:5550104827">Call Us</a>
  </div>

  <section class="testimonials abs" id="testimonials" role="img" aria-label="Red band with a faint town skyline drawing">
    <div class="rule abs"></div>
  </section>
  <h2 class="section-title testimonials-title abs">Testimonials</h2>

  <svg class="arrow abs" style="left:128px" width="24" height="36" viewBox="0 0 24 36"><path d="M20 2 L4 18 L20 34" fill="none" stroke="rgba(255,255,255,.8)" stroke-width="3"/></svg>
  <svg class="arrow abs" style="left:1052px" width="24" height="36" viewBox="0 0 24 36"><path d="M4 2 L20 18 L4 34" fill="none" stroke="rgba(255,255,255,.8)" stroke-width="3"/></svg>

  <blockquote class="quote-card quote-a abs">
    <div class="mark">&ldquo;</div>
    <p>Donec dictum lectus non odio Cras a ante vitae enim iaculis aliquam Mauris nunc quam venenatis nec euismod sit amet egestas placerat es</p>
    <div class="author">By Author Name</div>
  </blockquote>
  <blockquote class="quote-card quote-b abs">
    <div class="mark">&ldquo;</div>
    <p>Donec dictum lectus non odio Cras a ante vitae enim iaculis aliquam Mauris nunc quam venenatis nec euismod sit amet egestas placerat es</p>
    <div class="author">By Author Name</div>
  </blockquote>
  <div class="avatar avatar-a abs" role="img" aria-label="Portrait of a customer"></div>
  <div class="avatar avatar-b abs" role="img" aria-label="Portrait of a customer"></div>

  <footer>
    <nav class="footer-nav abs">
      <a href="#about">About</a><a href="#services">Services</a><a href="#car">Car</a><a href="#boat">Boat</a><a href="#airplanes">Airplanes</a><a href="#testimonials">Testimonials</a><a href="#contact">Contact</a>
    </nav>
    <p class="copyright abs">© 2018 Company Name &nbsp;All right reserved &nbsp;Terms of Use</p>
    <a class="footer-phone abs" href="tel:5550104827">
      <svg width="20" height="20" viewBox="0 0 24 24"><path fill="#e3151f" d="M6.6 10.8a15.1 15.1 0 0 0 6.6 6.6l2.2-2.2c.3-.3.7-.4 1-.2 1.1.4 2.3.6 3.6.6.6 0 1 .4 1 1V20c0 .6-.4 1-1 1C10.6 21 3 13.4 3 4c0-.6.4-1 1-1h3.5c.6 0 1 .4 1 1 0 1.3.2 2.5.6 3.6.1.3 0 .7-.2 1z"/></svg>
      555-010-4827
    </a>
    <div class="social abs">
      <a class="s1" href="#social-1" aria-label="Social profile 1"></a>
      <a class="s2" href="#social-2" aria-label="Social profile 2"></a>
      <a class="s3" href="#social-3" aria-label="Social profile 3"></a>
      <a class="s4" href="#social-4" aria-label="Social profile 4"></a>
      <a class="s5" href="#social-5" aria-label="Social profile 5"></a>
    </div>
  </footer>

</div>
</body>
</html>
```